KLR Buildworks - Civil Construction Construction Company (Telecommunications)

Need a basic website to refine our branding to a current reflection of our service offerings. KLR Buildworks provides civil construction services specializing in telecommunication sector.
I have started to create a website using word press. I would like to have someone refine the design and polish the overall look and functionality of the site. I would like to website to function in the wordpress format to allow for future edits and control of site.
Included site preview:
https://pvhosts-ua.pagemakerbench.example/7e2d94fa.com/Admin/index.html/qm_draft_view

```html
<!DOCTYPE html>
<html lang="en">
<head>
<meta charset="utf-8">
<title>KLR Buildworks – Civil Construction Company</title>
<link rel="stylesheet" href="https://fonts.googleapis.com/css2?family=Poppins:wght@300;400;500;600;700&family=Arimo:wght@400&display=swap">
<style>
:root{
  --red:#e81e25;
  --ink:#333538;
  --text:#4a4a4a;
  --muted:#6b6b6b;
  --line:#d5d5d5;
  --pale:#eef4fd;
  --black:#000;
  --white:#fff;
}
*{box-sizing:border-box;margin:0;padding:0}
html,body{width:1200px;height:3382px;overflow:hidden;background:var(--white)}
body{position:relative;font-family:'Poppins',sans-serif;color:var(--ink)}
.abs{position:absolute}

/* header */
.topline{left:0;top:0;width:1200px;height:5px;background:var(--red)}
.brand{font-family:'Poppins',sans-serif;font-weight:500;letter-spacing:.5px;display:flex;align-items:center;gap:10px}
.brand .mark{width:14px;height:14px;background:var(--red)}
.site-brand{left:112px;top:40px;font-size:30px;color:var(--black)}
.callus{right:110px;top:20px;display:flex;align-items:center;gap:8px;font-size:17px;color:var(--ink)}
.callus .ring{width:44px;height:44px;border:2px solid var(--red);border-radius:50%;display:flex;align-items:center;justify-content:center}
.mainnav{right:112px;top:79px;display:flex;gap:35px;font-size:13.5px;font-weight:500;color:var(--black)}
.mainnav a{color:inherit;text-decoration:none;position:relative}
.mainnav a.active{color:var(--red)}
.mainnav a.active:after{content:"";position:absolute;left:-4px;right:-6px;bottom:-8px;height:3px;background:var(--red);transform:skewY(-3deg)}

/* hero */
.hero{left:0;top:113px;width:1200px;height:690px;background:linear-gradient(160deg,#6f7a66 0%,#a8432e 35%,#8e3a2a 55%,#5d5c4e 80%,#7d7c70 100%)}
.hero-brand{left:0;top:380px;width:1200px;justify-content:center;font-size:62px;color:var(--white);font-weight:400;letter-spacing:1px}
.hero-brand .mark{width:22px;height:22px;background:var(--white)}
.hero-sub{left:0;top:464px;width:1200px;text-align:center;font-size:28px;font-weight:700;color:var(--white)}
.btn{display:flex;align-items:center;justify-content:center;background:var(--red);color:var(--white);font-weight:600;border-radius:40px;text-decoration:none}
.hero-btn{left:505px;top:524px;width:190px;height:64px;font-size:20px}
.dots{left:572px;top:734px;display:flex;gap:6px}
.dots span{width:15px;height:15px;border-radius:50%;background:var(--white)}
.dots span.on{background:var(--red)}
.hero-cut{left:0;top:740px;width:1200px;height:120px}

/* headings */
.sec-title{left:0;width:1200px;text-align:center;font-size:35px;font-weight:600;color:var(--ink)}
.sec-title:after{content:"";display:block;margin:4px auto 0;width:140px;height:10px;background:var(--red);clip-path:polygon(0 0,100% 0,92% 100%,8% 55%);transform:translateX(18px)}

/* why choose */
.card{top:995px;width:300px;height:400px;border:1px solid #8d8d8d;background:var(--white)}
.card .icon{position:absolute;left:0;top:28px;width:100%;height:104px;display:flex;justify-content:center}
.card ul{position:absolute;left:28px;right:16px;top:168px;list-style:none}
.card li{position:relative;padding-left:28px;font-size:16.5px;line-height:24px;color:var(--muted);font-weight:400;margin-bottom:31px}
.card li:before{content:"";position:absolute;left:2px;top:7px;width:11px;height:11px;border:2px solid var(--red);border-radius:50%;box-sizing:border-box}
.card li:after{content:"";position:absolute;left:5px;top:10px;width:3px;height:3px;border-right:1.5px solid var(--red);border-top:1.5px solid var(--red);transform:rotate(45deg)}
.card.tight li{margin-bottom:24px}

/* profile */
.profile{left:0;top:1457px;width:1200px;height:617px;background:var(--pale)}
.profile-photo{left:0;top:1733px;width:1200px;height:341px;background:linear-gradient(180deg,var(--pale) 0%,#b9b8a6 25%,#9b8f59 55%,#6f7a44 100%)}
.profile-text{left:225px;top:1566px;width:750px;text-align:center;font-family:'Arimo',Arial,sans-serif;font-size:13.5px;line-height:26px;color:var(--muted)}
.profile-btn{left:513px;top:1687px;width:174px;height:58px;font-size:17px}

/* work */
.tile{width:315px;height:262px}
.tile.feature{background:linear-gradient(180deg,#ee3a34,#e22b28);display:flex;align-items:center;justify-content:center;text-align:center;color:var(--white);font-weight:600;font-size:17px;line-height:30px}

/* footer */
.foot-shape{left:0;top:2813px;width:1200px;height:115px}
.footer{left:0;top:2926px;width:1200px;height:456px;background:var(--black);color:var(--white)}
.footnav{left:0;top:2945px;width:1200px;display:flex;justify-content:center;gap:36px;font-size:13px;font-weight:500;color:var(--white)}
.rule{left:112px;width:976px;height:1px;background:#2a2a2a}
.foot-h{top:3035px;font-size:21px;font-weight:600;color:var(--white);letter-spacing:.5px}
.field{background:var(--white);color:#555;font-size:11px;padding:10px 12px;font-family:Arial,sans-serif}
.submit{left:112px;top:3240px;width:98px;height:35px;background:var(--red);color:var(--white);font-size:13px;display:flex;align-items:center;justify-content:center}
.info{left:543px;display:flex;align-items:center;gap:14px;color:var(--white)}
.info .ring{width:44px;height:44px;border:1.5px solid var(--white);border-radius:50%;display:flex;align-items:center;justify-content:center;flex-shrink:0}
.info b{display:block;font-size:13px;font-weight:600}
.info span{font-size:12px;font-weight:400}
.foot-brand{left:820px;top:3090px;font-size:27px;color:var(--white);font-weight:400}
.foot-brand .mark{background:var(--white)}
.social{left:853px;top:3148px;display:flex;gap:5px}
.social span{width:38px;height:38px;border:1.5px solid var(--white);border-radius:50%}
.copy{left:0;top:3330px;width:1200px;text-align:center;font-size:14.5px;color:var(--white)}
</style>
</head>
<body>

<div class="abs topline"></div>
<div class="abs brand site-brand"><span class="mark"></span>KLR BUILDWORKS</div>
<div class="abs callus">
  <span class="ring"><svg width="18" height="18" viewBox="0 0 24 24"><path fill="#e81e25" d="M6.6 10.8a15 15 0 006.6 6.6l2.2-2.2a1 1 0 011-.25 11.4 11.4 0 003.6.57 1 1 0 011 1V20a1 1 0 01-1 1A17 17 0 013 4a1 1 0 011-1h3.5a1 1 0 011 1c0 1.25.2 2.45.57 3.57a1 1 0 01-.25 1z"/></svg></span>
  CALL US : 1 (587) 555-0148
</div>
<nav class="abs mainnav">
  <a class="active" href="#">HOME</a><a href="#">COMPANY PROFILE</a><a href="#">WHY CHOOSE US</a><a href="#">OUR WORK</a><a href="#">CONTACT</a>
</nav>

<section>
  <div class="abs hero" role="img" aria-label="Photo of a red tracked horizontal drilling rig with an operator beside rail tracks in a forest"></div>
  <div class="abs brand hero-brand"><span class="mark"></span>KLR BUILDWORKS</div>
  <div class="abs hero-sub">CIVIL CONSTRUCTION CONSTRUCTION COMPANY</div>
  <a class="abs btn hero-btn" href="#">READ MORE</a>
  <div class="abs dots"><span></span><span class="on"></span><span></span></div>
  <svg class="abs hero-cut" viewBox="0 0 1200 120" preserveAspectRatio="none">
    <polygon fill="#fff" points="0,20 1103,115 1200,115 1200,61 1153,61 0,8 0,20"/>
    <polygon fill="#fff" points="0,8 0,120 1200,120 1200,61"/>
    <polygon fill="#e81e25" points="0,8 1153,61 1103,115 0,22"/>
  </svg>
</section>

<section>
  <h2 class="abs sec-title" style="top:874px">WHY CHOOSE US</h2>

  <div class="abs card" style="left:112px">
    <div class="icon"><svg width="84" height="104" viewBox="0 0 84 104" fill="none" stroke-width="3">
      <path d="M42 3 L80 18 V52 C80 76 62 92 42 101 C22 92 4 76 4 52 V18 Z" stroke="#111"/>
      <rect x="28" y="46" width="28" height="22" rx="3" stroke="#e81e25"/>
      <path d="M33 46 V38 a9 9 0 0118 0 V46" stroke="#e81e25"/>
      <circle cx="42" cy="56" r="2" fill="#e81e25" stroke="none"/>
    </svg></div>
    <ul><li>Accredited health &amp; safety program</li><li>Proven track record of safety excellence</li><li>Continuous training &amp; development of employees</li></ul>
  </div>

  <div class="abs card" style="left:450px">
    <div class="icon"><svg width="92" height="92" viewBox="0 0 92 92" fill="none" stroke-width="3" style="margin-top:4px">
      <path d="M40 4h12l2 10 8 3 8-6 9 9-6 8 3 8 10 2v12l-10 2-3 8 6 8-9 9-8-6-8 3-2 10H40l-2-10-8-3-8 6-9-9 6-8-3-8-10-2V40l10-2 3-8-6-8 9-9 8 6 8-3z" stroke="#111"/>
      <circle cx="46" cy="46" r="22" stroke="#111"/>
      <path d="M34 30l10 10-3 5 22 22a4 4 0 01-6 6L35 51l-5 3-10-10 5-2 7 6 5-5-7-7z" stroke="#e81e25"/>
    </svg></div>
    <ul><li>Productive and efficient crews</li><li>Current fleet of modern equipment</li><li>Use of latest construction techniques/technologies</li></ul>
  </div>

  <div class="abs card tight" style="left:788px">
    <div class="icon"><svg width="96" height="96" viewBox="0 0 96 96" fill="none" stroke-width="3">
      <circle cx="48" cy="14" r="9" stroke="#e81e25"/><path d="M34 40a14 14 0 0128 0" stroke="#e81e25"/>
      <path d="M48 40v10M18 50h60M18 50v10M48 50v10M78 50v10" stroke="#e81e25"/>
      <circle cx="18" cy="68" r="8" stroke="#111"/><path d="M5 92a13 13 0 0126 0" stroke="#111"/>
      <circle cx="48" cy="68" r="8" stroke="#111"/><path d="M35 92a13 13 0 0126 0" stroke="#111"/>
      <circle cx="78" cy="68" r="8" stroke="#111"/><path d="M65 92a13 13 0 0126 0" stroke="#111"/>
    </svg></div>
    <ul><li>Quality and process driven</li><li>Excellent customer service</li><li>Privately owned and operated</li><li>Dependable, Reliable and Honest</li></ul>
  </div>
</section>

<section>
  <div class="abs profile"></div>
  <div class="abs profile-photo" role="img" aria-label="Photo of yellow trenching machines, an orange cable reel and a drilling unit in a grassy field by a lake"></div>
  <h2 class="abs sec-title" style="top:1491px">COMPANY PROFILE</h2>
  <p class="abs profile-text">KLR Buildworks is a safety conscious, productive and efficient construction firm capable of all facets of civil construction. have completed thousands of projects across Alberta, Saskatchewan and British Columbia working within various industry sectors. We have built a diverse team of skilled professionals who take a great deal of pride in their work and aim to achieve the highest levels of customer satisfaction.</p>
  <a class="abs btn profile-btn" href="#">READ MORE</a>
</section>

<section>
  <h2 class="abs sec-title" style="top:2117px">OUR WORK</h2>
  <div class="abs tile" style="left:112px;top:2211px;background:linear-gradient(160deg,#8b7f67,#9ba3a3 45%,#5d5f56)" role="img" aria-label="Aerial photo of a company shop building with service trucks parked outside"></div>
  <div class="abs tile feature" style="left:442px;top:2211px">HDD REDUCES SURFACE<br>DISRUPTION ON WORKSITES</div>
  <div class="abs tile" style="left:773px;top:2211px;background:linear-gradient(160deg,#a9bccc,#6f8a52 50%,#2c2d2a)" role="img" aria-label="Photo of a drilling rig set up on a residential lawn"></div>
  <div class="abs tile" style="left:112px;top:2485px;background:linear-gradient(160deg,#a7b9c9,#5f7d45 50%,#2a2b27)" role="img" aria-label="Photo of a worker in a safety vest operating a drill in a park"></div>
  <div class="abs tile" style="left:442px;top:2485px;background:linear-gradient(160deg,#4f6b38,#b99a3a 50%,#3e4d2a)" role="img" aria-label="Photo of a yellow trencher with a worker in a hard hat"></div>
  <div class="abs tile" style="left:773px;top:2485px;background:linear-gradient(160deg,#8a9a86,#8e3b2c 45%,#3d4430)" role="img" aria-label="Photo of a red drilling rig on a forest worksite"></div>
</section>

<footer>
  <svg class="abs foot-shape" viewBox="0 0 1200 115" preserveAspectRatio="none">
    <polygon fill="#000" points="0,56 40,56 1200,108 1200,115 0,115"/>
    <polygon fill="#e81e25" points="40,56 107,0 1200,90 1200,108"/>
  </svg>
  <div class="abs footer"></div>
  <nav class="abs footnav"><span>HOME</span><span>COMPANY PROFILE</span><span>WHY CHOOSE US</span><span>OUR WORK</span><span>CONTACT</span></nav>
  <div class="abs rule" style="top:3001px"></div>

  <h3 class="abs foot-h" style="left:112px">CONTACT US</h3>
  <div class="abs field" style="left:112px;top:3089px;width:180px;height:37px">First Name :</div>
  <div class="abs field" style="left:302px;top:3089px;width:180px;height:37px">Last Name :</div>
  <div class="abs field" style="left:112px;top:3134px;width:180px;height:36px">Email :</div>
  <div class="abs field" style="left:302px;top:3134px;width:180px;height:36px">Phone :</div>
  <div class="abs field" style="left:112px;top:3178px;width:370px;height:54px">Message :</div>
  <div class="abs submit">SUBMIT</div>

  <h3 class="abs foot-h" style="left:553px">ADDRESS</h3>
  <div class="abs info" style="top:3084px">
    <span class="ring"><svg width="14" height="18" viewBox="0 0 14 18"><path fill="none" stroke="#fff" stroke-width="1.6" d="M7 17s6-6.5 6-10A6 6 0 001 7c0 3.5 6 10 6 10z"/><circle cx="7" cy="7" r="2" fill="#fff"/></svg></span>
    <div><b>ADDRESS</b><span># Lorem Ipsum Dummy Lorem</span></div>
  </div>
  <div class="abs info" style="top:3145px">
    <span class="ring"><svg width="16" height="16" viewBox="0 0 24 24"><path fill="#fff" d="M6.6 10.8a15 15 0 006.6 6.6l2.2-2.2a1 1 0 011-.25 11.4 11.4 0 003.6.57 1 1 0 011 1V20a1 1 0 01-1 1A17 17 0 013 4a1 1 0 011-1h3.5a1 1 0 011 1c0 1.25.2 2.45.57 3.57a1 1 0 01-.25 1z"/></svg></span>
    <div><b>PHONE NUMBER</b><span>1 (587) 555-0148</span></div>
  </div>
  <div class="abs info" style="top:3206px">
    <span class="ring"><svg width="16" height="12" viewBox="0 0 16 12"><rect width="16" height="12" rx="1.5" fill="#fff"/><path d="M1 1l7 6 7-6" fill="none" stroke="#000" stroke-width="1.4"/></svg></span>
    <div><b>EMAIL US</b><span>info@klrbuildworks.example</span></div>
  </div>

  <div class="abs brand foot-brand"><span class="mark"></span>KLR BUILDWORKS</div>
  <div class="abs social"><span></span><span></span><span></span><span></span><span></span></div>

  <div class="abs rule" style="top:3302px"></div>
  <p class="abs copy">© Copyright 2022 KLR Buildworks .All Rights Reserved</p>
</footer>

</body>
</html>
```